Webdesign für Steuerberaterin
Zielgruppe
Ich bin Steuerberaterin. Meine Zielgruppe sind sowohl Privatpersonen als auch Unternehmer sowie Männer und Frauen.
Aufgabenstellung
Bitte mein Logo und Foto mit berücksichtigen. Ich möchte keine Website, auf der alle 'Reiter' als eine Seite von oben nach unten durchlaufen. Sondern wirklich einzelne, voneinander getrennte Seiten.

```html
<!DOCTYPE html>
<html lang="de">
<head>
<meta charset="utf-8">
<title>Maren Brodtke – Steuerberaterin</title>
<link rel="stylesheet" href="https://fonts.googleapis.com/css2?family=Source+Sans+3:wght@400;600&family=Tinos&display=swap">
<style>
  :root {
    --page-bg: #f1f1f1;
    --gold-top: #e4bd3f;
    --gold-bottom: #d3a626;
    --gold-text: #a67c27;
    --body-text: #565656;
    --rule: #6a6a6a;
    --white: #ffffff;
  }
  * { margin: 0; padding: 0; box-sizing: border-box; }
  html, body { width: 1200px; height: 1056px; overflow: hidden; }
  body {
    position: relative;
    background: var(--page-bg);
    font-family: "Source Sans 3", "Myriad Pro", sans-serif;
    color: var(--body-text);
  }
  .nav-band {
    position: absolute; left: 0; top: 10px; width: 1200px; height: 26px;
    background: linear-gradient(var(--gold-top), var(--gold-bottom));
  }
  .nav-link {
    position: absolute; top: 0; line-height: 26px;
    transform: translateX(-50%);
    color: var(--white); font-size: 11px; text-decoration: none;
    white-space: nowrap;
  }
  .brand-box {
    position: absolute; left: 517px; top: 0; width: 182px; height: 178px;
    background: var(--white);
    display: flex; flex-direction: column; align-items: center; justify-content: center;
    gap: 8px;
  }
  .brand-mark {
    width: 14px; height: 14px; border-radius: 50%;
    background: var(--gold-text);
  }
  .brand-name {
    font-size: 22px; font-weight: 600; color: var(--gold-text);
  }
  .brand-role {
    font-family: "Tinos", "Times New Roman", serif;
    font-size: 8.5px; letter-spacing: 2.4px; color: #333;
  }
  .portrait {
    position: absolute; left: 376px; top: 212px; width: 477px; height: 320px;
    background:
      radial-gradient(ellipse 40% 60% at 52% 70%, #1c2233 0%, #1c2233 55%, rgba(28,34,51,0) 56%),
      radial-gradient(ellipse at 50% 40%, #ffffff 0%, #e2e2e2 55%, #bdbdbd 100%);
  }
  .welcome-heading {
    position: absolute; left: 377px; top: 556px; width: 475px;
    display: flex; align-items: center; gap: 12px;
  }
  .welcome-heading .rule { flex: 1; height: 1px; background: var(--rule); }
  .welcome-heading h1 {
    font-family: "Tinos", "Times New Roman", serif;
    font-weight: 400; font-size: 24px; color: var(--gold-text);
    white-space: nowrap;
  }
  .welcome-text {
    position: absolute; left: 300px; top: 616px; width: 640px;
    text-align: center; font-size: 16px; line-height: 19.5px;
  }
  .welcome-text .lead { font-weight: 600; font-size: 16px; margin-bottom: 21px; }
  .welcome-text p { margin-bottom: 20px; }
  .footer-band {
    position: absolute; left: 0; bottom: 0; width: 1200px; height: 28px;
    background: linear-gradient(var(--gold-top), var(--gold-bottom));
  }
</style>
</head>
<body>
  <nav class="nav-band">
    <a class="nav-link" href="#" style="left:274px">Über mich</a>
    <a class="nav-link" href="#" style="left:393px">Leistungen</a>
    <a class="nav-link" href="#" style="left:794px">Kontakt</a>
    <a class="nav-link" href="#" style="left:908px">Impressum</a>
  </nav>

  <div class="brand-box">
    <span class="brand-mark"></span>
    <span class="brand-name">Maren Brodtke</span>
    <span class="brand-role">STEUERBERATERIN</span>
  </div>

  <div class="portrait" role="img" aria-label="Porträtfoto der Steuerberaterin vor heller Steinwand"></div>

  <div class="welcome-heading">
    <span class="rule"></span>
    <h1>Schön, dass Sie da sind</h1>
    <span class="rule"></span>
  </div>

  <div class="welcome-text">
    <p class="lead">Ich freue mich, dass Sie den Weg zu mir gefunden haben!</p>
    <p>Sie sind bei mir genau richtig:<br>
      Egal, ob Sie Privatperson sind, die Ihre Einkommensteuer-Erklärung<br>
      in vertrauensvolle Hände geben möchte,<br>
      oder Unternehmer, der sich z.B. das „Rundum-Sorglos-Paket“<br>
      mit Buchführung, Jahresabschluss und Steuererklärungen wünscht.</p>
    <p>Schauen Sie sich hier gerne um und melden Sie sich bei mir – ich bin bei jedem<br>
      steuerlichen Thema gerne Ihr kompetenter und zuverlässiger Ansprechpartner.</p>
    <p>Für mich ist es eine Selbstverständlichkeit,<br>
      dass ich auch nach mehr als 12 Jahren Berufserfahrung<br>
      durch permanente Fortbildungen immer auf dem aktuellsten Stand<br>
      der relevanten Gesetze und Verordnungen bin.<br>
      Nur so kann ich Sie bestmöglich beraten.</p>
  </div>

  <footer class="footer-band"></footer>
</body>
</html>
```